Vance Health & Fitness Website selling saunas and Cold tubs

www.dockvaultguys.com, www.frostlanterguys, www.chillharborguys
Design a website
We are selling saunas, infrared saunas, cold plunge tubs, and massage chairs to financially successful MEN.
We want professional, simple, masculine with a touch of sexy.
One section for each… saunas, cold plunge tubs, massage chairs.
Each will have at least two buy links to their affiliate/supplier/store.
The landing page / opening page / needs big & bold; a full screen image? a great picture showing the warmth of a sauna? Need your ideas
The pictures are everything.

The Website for our book
https://maebelsvigorguys.com/

Coding

Coded - Design and coding required

Number of Pages Required

1 page

Requirements
Must have
• Great pictures

```html
<!DOCTYPE html>
<html lang="en">
<head>
<meta charset="utf-8">
<title>Maebel Vance Fitness for Men</title>
<link rel="stylesheet" href="https://fonts.googleapis.com/css2?family=Oswald:wght@400;500;600&family=Roboto+Condensed:ital,wght@0,400;0,500;1,400&display=swap">
<style>
:root{
  --orange:#e9501f;
  --orange-2:#f07a2b;
  --ink:#2f2f2f;
  --dark:#141414;
  --white:#ffffff;
  --muted:#3a3a3a;
}
*{margin:0;padding:0;box-sizing:border-box}
html,body{width:1200px;height:3878px;overflow:hidden;background:var(--white)}
.page{position:relative;width:1200px;height:3878px;overflow:hidden;font-family:"Roboto Condensed",sans-serif;color:var(--ink)}
.abs{position:absolute}
.photo{position:absolute}
.display{font-family:"Oswald",sans-serif;font-weight:500}

/* hero */
.hero-photo{left:0;top:0;width:1200px;height:640px;
  background:radial-gradient(ellipse at 50% 30%,#5a5a5a 0%,#2a2a2a 40%,#080808 80%);
  clip-path:polygon(0 0,1200px 0,1200px 505px,113px 575px,113px 640px,0 640px)}
.brand{left:143px;top:60px;display:flex;align-items:center;gap:10px;color:var(--white);font-family:"Oswald",sans-serif;font-weight:500;font-size:18px;width:200px;line-height:1.2}
.brand .dot{width:14px;height:14px;border-radius:50%;background:var(--white);flex:none}
.menu{left:1027px;top:82px;width:28px;height:24px}
.menu span{display:block;height:4px;background:var(--white);border-radius:2px;margin-bottom:6px}

.hero-panel{left:143px;top:489px;width:911px;height:532px;
  background:linear-gradient(180deg,var(--orange) 0%,var(--orange-2) 100%);
  clip-path:polygon(0 113px,911px 0,911px 532px,0 437px)}
.hero-text{left:143px;width:911px;text-align:center;color:var(--white)}
.hero-kicker{top:606px;font-family:"Oswald",sans-serif;font-size:21px;line-height:33px;font-weight:400}
.hero-title{top:684px;font-family:"Oswald",sans-serif;font-weight:500;font-size:56px;line-height:66px;letter-spacing:-0.5px}
.hero-sub{top:838px;font-family:"Oswald",sans-serif;font-size:22px;line-height:33px;font-weight:400}

/* benefits */
.benefits-title{left:143px;top:1064px;font-size:55px;line-height:64px;letter-spacing:-0.8px;color:var(--ink)}
.benefits-lead{left:143px;top:1213px;font-family:"Oswald",sans-serif;font-weight:500;font-size:22px;color:var(--ink)}
.benefit-list{left:143px;top:1268px;list-style:none}
.benefit-list li{position:relative;padding-left:42px;height:37.5px;font-size:16px;line-height:30px;color:var(--muted)}
.benefit-list li::before{content:"";position:absolute;left:2px;top:12px;width:12px;height:12px;border-radius:50%;background:var(--orange)}
.benefits-note{left:143px;top:1466px;font-family:"Oswald",sans-serif;font-weight:500;font-size:22px;color:var(--ink)}
.runner{left:900px;top:1370px;width:300px;height:347px;background:radial-gradient(ellipse at 50% 50%,#4a4a4a 0%,#8a8a8a 45%,rgba(255,255,255,0) 70%)}

.flow-banner{left:143px;top:1551px;width:911px;height:316px;border-radius:158px;
  background:linear-gradient(135deg,#c84a1a 0%,#d9632a 50%,#c4501d 100%)}
.flow-text{left:143px;top:1645px;width:911px;text-align:center;color:var(--white);font-size:54px;line-height:60px}

/* testimonials */
.testi-bg{left:0;top:1867px;width:1200px;height:420px;
  background:linear-gradient(90deg,#e9e6e3 0%,#f4f2f0 40%,#fbfbfb 70%,#ffffff 100%)}
.testi-title{left:0;width:1200px;top:1930px;text-align:center;font-size:58px;color:var(--ink)}
.quote-mark{left:0;width:1200px;top:2010px;text-align:center;font-family:"Oswald",sans-serif;font-weight:600;font-size:90px;line-height:90px;color:var(--orange);font-style:italic}
.testi-quote{left:240px;width:720px;top:2090px;text-align:center;font-style:italic;font-size:16px;line-height:29.5px;color:var(--muted)}
.testi-name{left:0;width:1200px;top:2190px;text-align:center;font-family:"Oswald",sans-serif;font-size:19px;color:var(--orange)}
.arrow{width:38px;height:38px}

/* product sections */
.panel{background:linear-gradient(180deg,var(--orange) 0%,var(--orange-2) 100%)}
.product-title{font-size:42px;color:var(--white);letter-spacing:-0.5px}
.product-copy{width:440px;font-size:12.5px;line-height:22px;color:var(--white)}
.btn{position:absolute;height:42px;border-radius:21px;font-family:"Oswald",sans-serif;font-size:12px;text-align:center;line-height:40px;width:103px}
.btn-buy{background:var(--white);color:var(--orange);border:1px solid var(--white)}
.btn-contact{border:2px solid var(--white);color:var(--white)}

/* footer */
.footer{left:0;top:3697px;width:1200px;height:181px;background:var(--dark)}
.footer-brand{left:146px;top:3770px;color:var(--white);font-family:"Oswald",sans-serif;font-size:17px;display:flex;align-items:center;gap:10px;width:190px;line-height:1.2}
.footer-brand .dot{width:14px;height:14px;border-radius:50%;background:var(--white);flex:none}
.sub-title{left:354px;top:3737px;color:var(--white);font-family:"Oswald",sans-serif;font-size:20px}
.sub-field{left:355px;top:3788px;width:280px;height:40px;border-radius:20px;background:var(--white)}
.sub-field span{position:absolute;left:28px;top:12px;font-size:11px;color:#444}
.sub-btn{left:531px;top:3788px;width:104px;height:40px;border-radius:20px;background:var(--orange);color:var(--white);font-family:"Oswald",sans-serif;font-size:13px;text-align:center;line-height:40px}
.foot-nav{left:709px;top:3741px;list-style:none;color:var(--white);font-family:"Oswald",sans-serif;font-size:13.5px}
.foot-nav li{height:27.7px}
.legal{left:852px;top:3741px;color:var(--white);font-family:"Oswald",sans-serif;font-size:13.5px;line-height:27.7px}
.social{top:3810px;width:25px;height:25px;border-radius:50%;background:var(--white)}
</style>
</head>
<body>
<div class="page">

  <!-- hero -->
  <div class="photo hero-photo" role="img" aria-label="Muscular man and woman training with dumbbells against a dark textured wall"></div>
  <div class="abs brand"><span class="dot"></span>Maebel Vance Fitness</div>
  <div class="abs menu" aria-label="Menu"><span></span><span></span><span></span></div>

  <div class="abs hero-panel"></div>
  <p class="abs hero-text hero-kicker">Maebel Vance Fitness for Men<br>Top of the Line Health Products Exclusively for the Financially Successful</p>
  <h1 class="abs hero-text hero-title">Dramatically Improve Your Health<br>Without Exercise</h1>
  <p class="abs hero-text hero-sub">Successful Men Recognize the Importance of Their Health<br>and Make it a Priority.&nbsp; It’s Your Time.&nbsp; You’ve Earned it.</p>

  <!-- benefits -->
  <h2 class="abs display benefits-title">A Mans Body Thrives on Circulation<br>And It Doesn’t Care How You Get It</h2>
  <p class="abs benefits-lead">When there’s no time for exercise. use Hot, Cold, or Massage. The Benefits are Numerous.</p>
  <ul class="abs benefit-list">
    <li>Relieve Stress&nbsp; -&nbsp; Detox Your Pores&nbsp; -&nbsp; Sleep Better</li>
    <li>Relieve Muscle Tension&nbsp; -&nbsp; Boost Energy Levels</li>
    <li>Increase Testosterone&nbsp; -&nbsp; Reduce Inflammation&nbsp; -&nbsp; Increase Immunity&nbsp; Reduce Depression&nbsp; -&nbsp; Alleviate Joint Pain&nbsp; -&nbsp; Healthier Skin</li>
    <li>Lower the Risk of Cardiovascular Disease&nbsp; -&nbsp; Increase Metabolism</li>
    <li>Promote Weight Loss&nbsp; -&nbsp; A Longer &amp; Healthier Life</li>
  </ul>
  <p class="abs benefits-note">Specific Improvements will be Individual to You.</p>

  <div class="abs flow-banner" role="img" aria-label="Warm sauna interior tinted orange"></div>
  <h2 class="abs display flow-text">Everything Works Better with<br>Increased Blood Flow</h2>
  <div class="photo runner" role="img" aria-label="Athletic man sprinting forward"></div>

  <!-- testimonials -->
  <div class="photo testi-bg" role="img" aria-label="Faded photo of a woman relaxing with hands behind her head"></div>
  <h2 class="abs display testi-title">Testimonials</h2>
  <div class="abs quote-mark">“</div>
  <p class="abs testi-quote">“I climb in my sauna half asleep every morning for 20 minutes before I take a shower and head off to work. It’s the only thing I found that really wakes me up in the morning. I’m not a coffee drinker so that’s never been an option but this sauna is the perfect morning wake up.”</p>
  <p class="abs testi-name">Customer Name</p>
  <svg class="abs arrow" style="left:144px;top:2101px" viewBox="0 0 38 38" aria-label="Previous"><circle cx="19" cy="19" r="17" fill="none" stroke="#222" stroke-width="2"/><path d="M27 19H11M17 12l-7 7 7 7" fill="none" stroke="#222" stroke-width="2"/></svg>
  <svg class="abs arrow" style="left:1017px;top:2101px" viewBox="0 0 38 38" aria-label="Next"><circle cx="19" cy="19" r="17" fill="none" stroke="#222" stroke-width="2"/><path d="M11 19h16M21 12l7 7-7 7" fill="none" stroke="#222" stroke-width="2"/></svg>

  <!-- saunas -->
  <div class="photo" style="left:0;top:2263px;width:599px;height:451px;background:linear-gradient(135deg,#6b3a1c 0%,#b0713e 45%,#d9a574 75%,#8a5530 100%)" role="img" aria-label="Woman wrapped in a towel sitting in a wooden sauna"></div>
  <div class="abs panel" style="left:526px;top:2304px;width:528px;height:369px;clip-path:polygon(0 78px,528px 0,528px 306px,0 369px)"></div>
  <h3 class="abs display product-title" style="left:584px;top:2404px">SAUNAS</h3>
  <p class="abs product-copy" style="left:584px;top:2470px">Lorem ipsum dolor sit amet, consectetur adipiscing elit, sed do eiusmod tempor incididunt ut labore et dolore magna aliqua. Ut enim ad minim veniam, quis nostrud exercitation ullamco laboris nisi ut aliquip ex ea commodo consequat. Duis aute irure dolor in reprehenderit in voluptate velit esse cillum dolore</p>
  <a class="btn btn-buy" style="left:586px;top:2580px">BUY NOW</a>
  <a class="btn btn-contact" style="left:697px;top:2580px">CONTACT US</a>

  <!-- cold plunge -->
  <div class="photo" style="left:599px;top:2726px;width:601px;height:452px;background:linear-gradient(180deg,#1d2c52 0%,#3a4a86 40%,#1b2438 75%,#0c1118 100%)" role="img" aria-label="Woman in a cold plunge tub at night with candles"></div>
  <div class="abs panel" style="left:143px;top:2764px;width:530px;height:371px;clip-path:polygon(0 82px,530px 0,530px 308px,0 371px)"></div>
  <div class="photo" style="left:524px;top:2744px;width:90px;height:110px;background:linear-gradient(180deg,#3a3f52 0%,#1c1f2a 100%);border-radius:18px 18px 8px 8px" role="img" aria-label="Black massage chair product"></div>
  <h3 class="abs display product-title" style="left:202px;top:2866px">COLD PLUNGE TUBS</h3>
  <p class="abs product-copy" style="left:202px;top:2932px">Lorem ipsum dolor sit amet, consectetur adipiscing elit, sed do eiusmod tempor incididunt ut labore et dolore magna aliqua. Ut enim ad minim veniam, quis nostrud exercitation ullamco laboris nisi ut aliquip ex ea commodo consequat. Duis aute irure dolor in reprehenderit in voluptate velit esse cillum dolore</p>
  <a class="btn btn-buy" style="left:203px;top:3042px">BUY NOW</a>
  <a class="btn btn-contact" style="left:316px;top:3042px">CONTACT US</a>

  <!-- massage chairs -->
  <div class="photo" style="left:0;top:3188px;width:599px;height:450px;background:linear-gradient(135deg,#d8c8ae 0%,#c98f5f 35%,#d5482a 65%,#b8321c 100%)" role="img" aria-label="Man in red shirt receiving a shoulder massage on a massage chair"></div>
  <div class="abs panel" style="left:526px;top:3230px;width:528px;height:369px;clip-path:polygon(0 79px,528px 0,528px 309px,0 369px)"></div>
  <h3 class="abs display product-title" style="left:584px;top:3328px">MASSAGE CHAIRS</h3>
  <p class="abs product-copy" style="left:584px;top:3394px">Lorem ipsum dolor sit amet, consectetur adipiscing elit, sed do eiusmod tempor incididunt ut labore et dolore magna aliqua. Ut enim ad minim veniam, quis nostrud exercitation ullamco laboris nisi ut aliquip ex ea commodo consequat. Duis aute irure dolor in reprehenderit in voluptate velit esse cillum dolore</p>
  <a class="btn btn-buy" style="left:586px;top:3506px">BUY NOW</a>
  <a class="btn btn-contact" style="left:697px;top:3510px">CONTACT US</a>
  <div class="photo" style="left:964px;top:3456px;width:211px;height:241px;background:radial-gradient(ellipse at 50% 60%,#6a6a6a 0%,#9a9a9a 40%,rgba(255,255,255,0) 70%)" role="img" aria-label="Bodybuilder lifting a barbell overhead"></div>

  <!-- footer -->
  <footer class="abs footer"></footer>
  <div class="abs footer-brand"><span class="dot"></span>Maebel Vance Fitness</div>
  <p class="abs sub-title">SUBSCRIBE FOR UPDATES</p>
  <div class="abs sub-field"><span>Enter Email</span></div>
  <div class="abs sub-btn">SUBSCRIBE</div>
  <ul class="abs foot-nav"><li>HOME</li><li>ABOUT</li><li>PRODUCTS</li><li>CONTACT US</li></ul>
  <p class="abs legal">Copyright © 2024&nbsp; Vance Health &amp; Fitness<br>All Rights Reserved&nbsp; |&nbsp; Privacy</p>
  <span class="abs social" style="left:852px" aria-label="Social link"></span>
  <span class="abs social" style="left:890px" aria-label="Social link"></span>
  <span class="abs social" style="left:928px" aria-label="Social link"></span>

</div>
</body>
</html>
```